Print materials for 3-star hotel

We are changing up our print materials (notepads, letterheads, key card jackets, small flyer for the room rates) We are a 3 star business hotel in the Philippines and have mainly used grey tones and clean, simple lines. See attached photos for logo and hotel interior photos.

Target Market(s)

Business

Contact Information for Business Card

Corvale Terrace Hotel
Lindwell Banca Avenue corner Tolenta St Cebu City 6000 Philippines
Tel: +63 32 481 7302
Mobile: +63 917 648 2095
www.corvaleterracehotel.example

Font styles to use
Serif
Sans Serif

Requirements
Must have
• Simple
• Readable font and font size
Nice to have
• Neutral colors, grey and taupes
Should not have
• No purples and bright blues

```html
<!DOCTYPE html>
<html lang="en">
<head>
<meta charset="utf-8">
<title>Corvale Terrace Hotel – Business Card</title>
<link href="https://fonts.googleapis.com/css2?family=Cinzel:wght@400;500&family=Jost:wght@400&display=swap" rel="stylesheet">
<style>
  :root {
    --backdrop: #e4e3e1;
    --card-front: #ecebe8;
    --card-back: #f6f6f4;
    --foil: #b98a5e;
    --foil-light: #d9c7ae;
    --shadow: rgba(60, 55, 50, 0.18);
  }
  * { margin: 0; padding: 0; box-sizing: border-box; }
  html, body { width: 1200px; height: 900px; overflow: hidden; }
  body {
    background: var(--backdrop);
    position: relative;
    font-family: "Jost", sans-serif;
  }
  .card {
    position: absolute;
    left: 285px;
    width: 630px;
    height: 360px;
    box-shadow: 0 10px 28px var(--shadow);
  }
  .card--back {
    top: 60px;
    background: var(--card-back);
    display: flex;
    flex-direction: column;
    align-items: center;
    justify-content: center;
    gap: 22px;
  }
  .brand-square {
    width: 58px;
    height: 58px;
    background: var(--foil);
  }
  .brand-name {
    font-family: "Cinzel", serif;
    font-weight: 400;
    color: var(--foil);
    font-size: 30px;
    letter-spacing: 0.22em;
    text-align: center;
    line-height: 1.35;
  }
  .brand-name span { display: block; font-size: 17px; letter-spacing: 0.5em; }

  .card--front {
    top: 480px;
    background: linear-gradient(135deg, #f1f0ed 0%, var(--card-front) 55%, #e2e0dc 100%);
  }
  .holder {
    position: absolute;
    left: 46px;
    top: 40px;
    font-family: "Cinzel", serif;
    color: var(--foil);
  }
  .holder__name { font-size: 28px; font-weight: 400; letter-spacing: 0.04em; line-height: 1.1; }
  .holder__title { font-size: 18px; font-weight: 500; letter-spacing: 0.06em; }

  .contact {
    position: absolute;
    left: 46px;
    top: 150px;
    width: 390px;
    color: var(--foil);
    font-size: 17px;
    line-height: 1.3;
    list-style: none;
  }
  .contact__address { margin-bottom: 4px; }
  .contact__row { display: flex; align-items: center; gap: 12px; }
  .contact__row svg { width: 15px; height: 15px; flex: none; fill: var(--foil); }

  .front-mark {
    position: absolute;
    right: 56px;
    top: 96px;
    width: 120px;
    height: 120px;
    background: var(--foil-light);
  }
</style>
</head>
<body>
  <section class="card card--back" aria-label="Card back">
    <div class="brand-square"></div>
    <h1 class="brand-name">Corvale Terrace<span>Hotel</span></h1>
  </section>

  <section class="card card--front" aria-label="Card front">
    <div class="holder">
      <p class="holder__name">ELIAS MARREN</p>
      <p class="holder__title">PRESIDENT</p>
    </div>

    <ul class="contact">
      <li class="contact__address">Lindwell Banca Avenue corner Tolenta St<br>Cebu City 6000 Philippines</li>
      <li class="contact__row">
        <svg viewBox="0 0 16 16"><path d="M2 5c0-2 3-3 6-3s6 1 6 3v1h-3V5H5v1H2zM4 7h8l2 7H2z"/></svg>
        +63 32 481 7302
      </li>
      <li class="contact__row">
        <svg viewBox="0 0 16 16"><path d="M4 1h8v14H4zM5.5 3v9h5V3z"/></svg>
        +63 917 648 2095
      </li>
      <li class="contact__row">
        <svg viewBox="0 0 16 16"><path d="M4 1h7v4H4zM1 6h14v7H1zM4 11h8v4H4z"/></svg>
        +63 32 481 7318
      </li>
      <li class="contact__row">
        <svg viewBox="0 0 16 16"><path d="M1 3h14v10H1zM2 4l6 5 6-5v1L8 10 2 5z" fill-rule="evenodd"/></svg>
        elias@corvaleterrace.example
      </li>
      <li class="contact__row">
        <svg viewBox="0 0 16 16"><circle cx="8" cy="8" r="7"/></svg>
        www.corvaleterracehotel.example
      </li>
    </ul>

    <div class="front-mark"></div>
  </section>
</body>
</html>
```